Flat bootstrap design for existing site

I'm looking for a modern flat design based around an existing logo. This has to be a custom design (no external templates), and implemented into a bootstrap framework.

The logo is attached as 2 versions - choose whichever you want, that flows better with whatever design you choose.

Added screenshots of the existing site (currently using the default bootstrap layouts). Please make your designs around those pages in the screenshots (i.e. the homepage only has the postal code input and the header). The active page has 3 screenshots, because I wanted to illustrate the other states that would be visible (in the table rows).

This is a moving/junk removal website, just for some context.

Here's some example websites (flat designs) that I like, just to give you an idea of what I'm after.

https://www.plimvora.com/
https://dacklow.com/
https://trevanu.com/
https://quobrintal.com/en/

Coding

Coded - Design and coding required

Number of Pages Required

5+ page

Colors

Designer to choose colors to be used in the design.

Requirements
Must have
• It must be a modern/simple flat design, that is built around the existing logo (attached).
• It has to be implemented using bootstrap.

```html
<!DOCTYPE html>
<html lang="en">
<head>
<meta charset="utf-8">
<title>HAULVO – Booking</title>
<link href="https://fonts.googleapis.com/css2?family=Open+Sans:wght@400;600;700&display=swap" rel="stylesheet">
<style>
:root{
  --brand:#4bc8f5;
  --brand-dark:#41b4dc;
  --panel:#f3f3f3;
  --panel-border:#dadada;
  --row-alt:#e6e6e6;
  --text:#222;
  --accepted:#74b25a;
  --sent:#6fbfe0;
  --pending:#777;
  --white:#fff;
}
*{box-sizing:border-box;margin:0;padding:0}
html,body{width:1200px;height:974px;overflow:hidden;background:var(--white);font-family:"Open Sans",sans-serif;color:var(--text)}
.site-header{position:absolute;left:0;top:0;width:1200px;height:81px;background:var(--brand)}
.brand{position:absolute;left:99px;top:22px;display:flex;align-items:center;gap:8px;color:var(--white);font-weight:700;font-size:30px;letter-spacing:1px}
.brand-dot{width:20px;height:20px;border-radius:50%;background:var(--white)}
.main-nav{position:absolute;left:0;top:0;height:81px;width:1200px}
.main-nav a{position:absolute;top:0;height:81px;line-height:79px;color:var(--white);text-decoration:none;font-weight:700;font-size:15px}
.nav-book{left:458px}
.nav-how{left:555px}
.nav-driver{left:697px;width:191px;text-align:center;background:var(--brand-dark)}
.nav-account{left:915px}
.nav-account svg{margin-left:10px;vertical-align:middle}
.booking-panel{position:absolute;left:99px;top:121px;width:1002px;height:397px;background:var(--panel);border:2px solid var(--panel-border);border-radius:3px}
.panel-title{position:absolute;left:18px;top:22px;font-size:21px;font-weight:600;color:var(--brand)}
.field-label{position:absolute;font-size:15.5px;font-weight:600}
.field{position:absolute;background:var(--white);border:1px solid #ccc;border-radius:3px;font-size:14.5px;padding:0 12px;display:flex;align-items:center;justify-content:space-between}
.field-textarea{align-items:flex-start;padding-top:9px}
.btn-update{position:absolute;left:19px;top:322px;width:110px;height:39px;background:var(--brand);color:var(--white);border:none;border-radius:3px;font-family:inherit;font-size:16px;font-weight:600;letter-spacing:.5px}
.section-title{position:absolute;left:98px;top:553px;font-size:24.5px;font-weight:600;color:var(--brand)}
.notice{position:absolute;left:99px;top:605px;width:1002px;height:47px;background:var(--brand);color:var(--white);font-size:15.5px;font-weight:600;line-height:47px;padding-left:15px}
.drivers-table{position:absolute;left:99px;top:684px;width:1002px;height:250px;border:2px solid var(--panel-border);border-radius:3px;overflow:hidden}
.row{position:relative;height:48px;background:var(--panel);font-size:15px;font-weight:600}
.row:nth-child(odd){background:var(--row-alt)}
.row.head{height:50px;background:var(--brand);color:var(--white);font-size:16px}
.row.head:nth-child(odd){background:var(--brand)}
.cell{position:absolute;top:0;height:100%;display:flex;align-items:center}
.c-name{left:17px}.c-dist{left:205px}.c-time{left:394px}.c-pay{left:763px}
.badge{position:absolute;left:575px;top:9px;width:115px;height:30px;color:var(--white);font-size:15px;font-weight:600;display:flex;align-items:center;justify-content:center}
.badge.accepted{background:var(--accepted)}
.badge.sent{background:var(--sent)}
.badge.pending{background:var(--pending)}
</style>
</head>
<body>
<header class="site-header">
  <div class="brand"><span class="brand-dot"></span>HAULVO</div>
  <nav class="main-nav">
    <a class="nav-book" href="#">BOOK</a>
    <a class="nav-how" href="#">HOW IT WORKS</a>
    <a class="nav-driver" href="#">BECOME A DRIVER</a>
    <a class="nav-account" href="#">sam4@plorvent.com<svg width="10" height="6" viewBox="0 0 10 6"><path d="M0 0h10L5 6z" fill="#fff"/></svg></a>
  </nav>
</header>

<section class="booking-panel">
  <h2 class="panel-title">Booking Details:</h2>
  <label class="field-label" style="left:18px;top:92px">Package selected:</label>
  <div class="field" style="left:19px;top:116px;width:460px;height:39px">Package 1
    <svg width="10" height="16" viewBox="0 0 10 16"><path d="M5 0l5 6H0zM5 16l5-6H0z" fill="#333"/></svg></div>
  <label class="field-label" style="left:515px;top:92px">Pick-up time selected:</label>
  <div class="field" style="left:516px;top:116px;width:460px;height:39px">July 18 at 4:13 am
    <svg width="13" height="14" viewBox="0 0 13 14"><rect x="0.5" y="2" width="12" height="11.5" fill="none" stroke="#333"/><rect x="0.5" y="2" width="12" height="3" fill="#333"/><path d="M3 0v3M10 0v3M3 7h7M3 10h7M5 5v8M8 5v8" stroke="#333"/></svg></div>
  <label class="field-label" style="left:18px;top:186px">Description:</label>
  <div class="field field-textarea" style="left:19px;top:210px;width:957px;height:90px">1 large stove</div>
  <button class="btn-update">UPDATE</button>
</section>

<h2 class="section-title">Drivers in your area</h2>
<div class="notice">Please stay on this page and be patient, while we contact the drivers and find you one ASAP.</div>

<div class="drivers-table">
  <div class="row head"><span class="cell c-name">Name</span><span class="cell c-dist">Distance (km)</span><span class="cell c-time">Agreed pick-up time</span></div>
  <div class="row"><span class="cell c-name">Owen Marsh</span><span class="cell c-dist">4.04km away</span><span class="cell c-time">July 18 at 4:13 am</span><span class="badge accepted">Time accepted</span><span class="cell c-pay">Payment made</span></div>
  <div class="row"><span class="cell c-name">Felix Grant</span><span class="cell c-dist">5.7km away</span><span class="cell c-time">-</span><span class="badge sent">Request sent</span></div>
  <div class="row"><span class="cell c-name">Dylan Pryce</span><span class="cell c-dist">11.13km away</span><span class="cell c-time">-</span><span class="badge sent">Request sent</span></div>
  <div class="row"><span class="cell c-name">Marco Hale</span><span class="cell c-dist">11.91km away</span><span class="cell c-time">-</span><span class="badge pending">Pending</span></div>
</div>
</body>
</html>
```